Business Card Design for Mortgage Broking Business

We need to redesign the business card. Mortgage broking business, doing home loan and commercial loans, existing logo, also QLBT member logo. design style needs to be simple, professional, elegant.

once final, need to setup for a team of different names and contact details.

Industry/Entity Type

Loan

Contact Information for Business Card

Name; Mobile; Email; Address; Tel; Fax; Australian Credit Licence: 618204

```html
<!DOCTYPE html>
<html lang="en">
<head>
<meta charset="utf-8">
<title>Harbourline Finance – Business Card</title>
<link rel="stylesheet" href="https://fonts.googleapis.com/css2?family=Tinos:wght@400;700&family=Archivo+Narrow:wght@600;700&family=Roboto:wght@700&display=swap">
<style>
  :root {
    --bg: #1c1c1e;
    --card-white: #ffffff;
    --brand-blue: #2b2f8f;
    --brand-violet: #5b60aa;
    --brand-green: #4dae69;
    --ink: #1e1e22;
    --ink-soft: #555559;
    --badge-blue: #2f4f8f;
  }
  * { margin: 0; padding: 0; box-sizing: border-box; }
  html, body { width: 1200px; height: 871px; overflow: hidden; background: var(--bg); }

  .canvas { position: relative; width: 1200px; height: 871px; }

  .card {
    position: absolute;
    width: 560px;
    height: 320px;
    left: 320px;
    overflow: hidden;
    background: var(--card-white);
  }
  .card--back { top: 70px; }
  .card--front { top: 470px; }

  /* Back side */
  .back-art { position: absolute; inset: 0; }
  .back-content {
    position: absolute;
    left: 20px; top: 0;
    width: 420px; height: 320px;
    text-align: center;
  }
  .brand {
    display: inline-flex;
    align-items: center;
    gap: 12px;
    font-family: "Tinos", serif;
    font-weight: 700;
    color: var(--brand-violet);
    white-space: nowrap;
  }
  .brand__mark { display: inline-block; flex: none; background: var(--brand-violet); }
  .back-content .brand { margin-top: 92px; font-size: 36px; }
  .back-content .brand__mark { width: 34px; height: 34px; }
  .services {
    margin-top: 30px;
    font-family: "Roboto", sans-serif;
    font-weight: 700;
    font-size: 19px;
    letter-spacing: 0.5px;
    color: var(--ink-soft);
  }
  .website {
    margin-top: 34px;
    font-family: "Roboto", sans-serif;
    font-weight: 700;
    font-size: 20px;
    letter-spacing: 0.5px;
    color: var(--ink-soft);
  }
  .website__tld { color: var(--brand-blue); }

  /* Front side */
  .front-brand {
    position: absolute;
    left: 28px; top: 80px;
    width: 226px;
  }
  .front-brand .brand {
    font-size: 28px;
    line-height: 1.1;
    gap: 12px;
    white-space: normal;
  }
  .front-brand .brand__mark { width: 28px; height: 28px; }
  .divider {
    position: absolute;
    left: 272px; top: 58px;
    width: 2px; height: 112px;
    background: var(--brand-blue);
  }
  .contact { position: absolute; left: 292px; top: 62px; }
  .contact__name {
    font-family: "Tinos", serif;
    font-weight: 400;
    font-size: 31px;
    letter-spacing: 1px;
    color: var(--ink);
    margin-bottom: 6px;
  }
  .contact__line {
    display: flex;
    align-items: center;
    gap: 8px;
    font-family: "Archivo Narrow", sans-serif;
    font-weight: 700;
    font-size: 15px;
    color: var(--ink);
    height: 22px;
    white-space: nowrap;
  }
  .contact__icon { width: 12px; height: 12px; flex: none; fill: var(--brand-blue); }

  .band { position: absolute; height: 12px; top: 238px; }
  .band--blue { left: 0; width: 392px; background: var(--brand-blue); }
  .band--green { left: 540px; width: 20px; background: var(--brand-green); }
  .member-badge {
    position: absolute;
    left: 408px; top: 222px;
    width: 122px; height: 42px;
    border: 3px solid var(--badge-blue);
    background: var(--card-white);
  }
</style>
</head>
<body>
<main class="canvas">

  <section class="card card--back" aria-label="Business card, back">
    <svg class="back-art" width="560" height="320" viewBox="0 0 560 320" aria-hidden="true">
      <rect width="560" height="320" fill="var(--brand-green)"/>
      <polygon points="330,0 560,0 560,320 390,320" fill="var(--brand-blue)"/>
      <ellipse cx="235" cy="150" rx="235" ry="185" fill="var(--card-white)"/>
    </svg>
    <div class="back-content">
      <div class="brand"><span class="brand__mark"></span>Harbourline Finance</div>
      <p class="services">Home Loan | Commercial Loan</p>
      <p class="website">yourwebsite<span class="website__tld">.com</span></p>
    </div>
  </section>

  <section class="card card--front" aria-label="Business card, front">
    <div class="front-brand">
      <div class="brand"><span class="brand__mark"></span><span class="brand__name">Harbourline Finance</span></div>
    </div>
    <div class="divider"></div>
    <div class="contact">
      <p class="contact__name">Your Name</p>
      <p class="contact__line">
        <svg class="contact__icon" viewBox="0 0 12 12" aria-hidden="true"><path d="M6 0a4.2 4.2 0 0 0-4.2 4.2C1.8 7.4 6 12 6 12s4.2-4.6 4.2-7.8A4.2 4.2 0 0 0 6 0zm0 5.9a1.7 1.7 0 1 1 0-3.4 1.7 1.7 0 0 1 0 3.4z"/></svg>
        1212 somewhere, Anywhere , Anywhere
      </p>
      <p class="contact__line">
        <svg class="contact__icon" viewBox="0 0 12 12" aria-hidden="true"><path d="M1 4.5C1 2.5 3 1.5 6 1.5s5 1 5 3H8.5V3.5h-5v1zM2.5 5.5h7l1.5 5H1z"/></svg>
        000-000-000
      </p>
      <p class="contact__line">
        <svg class="contact__icon" viewBox="0 0 12 12" aria-hidden="true"><path d="M0 2.5h12v7H0zM1 3.3v.4L6 7l5-3.3v-.4z"/></svg>
        Email@
      </p>
    </div>
    <div class="band band--blue"></div>
    <div class="member-badge" role="img" aria-label="Industry membership badge"></div>
    <div class="band band--green"></div>
  </section>

</main>
</body>
</html>
```